Company brochure

I would like to redesign our existing brochure.
It shall be trifold brochure with more modern and better appealing design than the old one. I am uploading the old one. The new design shall have all all information repeated from old brochure. It could be more or less pictures. I will provide more pictures if required. The keep text is important, the font shall be more modern. Brochure size shall be trifoldt US Legal size paper 8.5" x 14". I will provide all pitures, logos etc in a original format after design concept will be established or before on request.

Industry/Entity Type

It Company

Font styles to use
Other font styles liked:
• calibri

Colors
0555a3
3176b5
85abd2
0692cd
33a6d7
85cae6
1ab09a
33b8a4
87cfc6

Requirements
Nice to have
• I need all information from existing brochure such as text, customer logos, professional assos. logos to be shown in a new one. Picture could be added more.
Should not have
• No changes allowed to company letterhead. Only slight modifications allowed to company logo

```html
<!DOCTYPE html>
<html lang="en">
<head>
<meta charset="utf-8">
<title>Northbay Cooling &amp; Climate Systems – Trifold Brochure</title>
<link href="https://fonts.googleapis.com/css2?family=Raleway:wght@500;600&family=Open+Sans:wght@400;600&family=Roboto:wght@300;400&display=swap" rel="stylesheet">
<style>
  :root{
    --stage:#0d0d0f;
    --navy:#2b2f7f;
    --navy-deep:#262a6d;
    --ink-on-orange:#2a3a8e;
    --orange:#f6a821;
    --white:#ffffff;
  }
  *{box-sizing:border-box;margin:0;padding:0}
  html,body{width:1200px;height:1200px;overflow:hidden;background:var(--stage)}
  .spread{position:absolute;left:30px;top:254px;width:1140px;height:691px;background:var(--navy-deep);color:var(--white);font-family:"Open Sans",sans-serif}
  .top-band{height:14px;background:var(--navy)}
  .panels{position:relative;height:627px;display:flex}
  .panel{position:relative;width:380px;height:627px;overflow:hidden}
  .panel--left{background:linear-gradient(180deg,#2462b6 0%,#1f6ac0 40%,#2a63b8 100%)}
  .panel--mid{background:linear-gradient(160deg,#2d4fae 0%,#3762bf 45%,#2b4aa8 100%)}
  .panel--right{background:linear-gradient(180deg,#2f4db0 0%,#3458b8 100%)}
  h2{font-family:"Raleway",sans-serif;font-weight:600;font-size:19px;line-height:1.2;letter-spacing:.2px}
  p{font-size:9.4px;line-height:1.45;text-align:justify;hyphens:auto}
  .label{position:absolute;background:var(--navy);font-family:"Roboto",sans-serif;font-weight:300;color:var(--white)}
  .photo{position:absolute}
  .experience{position:absolute;left:0;top:0;width:380px;height:123px;background:#2160b4;padding:10px 33px 0 34px}
  .experience h2{margin-bottom:7px}
  .photo-row{position:absolute;left:0;top:123px;width:380px;height:137px;display:flex;gap:2px}
  .photo-row .photo{position:static;flex:1}
  .ph-plant{background:linear-gradient(180deg,#b8c4cc,#4f7d82 70%,#3a5e62)}
  .ph-tank{background:linear-gradient(180deg,#a9b2b8,#dfe3e5 45%,#7a8a90)}
  .ph-room{background:linear-gradient(180deg,#e2e7ea,#b9c4cb 60%,#8e9ca4)}
  .label--design{left:0;top:262px;width:250px;height:70px;padding:9px 0 0 34px;font-size:20px;line-height:1.22}
  .projects{position:absolute;left:34px;top:349px;width:315px}
  .projects h2{margin-bottom:6px}
  .projects li{list-style:none;font-size:9.4px;line-height:1.45;margin-bottom:13px}
  .service{position:absolute;left:50px;top:10px;width:280px}
  .service h2{margin-bottom:7px}
  .service p{margin-bottom:13px}
  .label--emergency{left:0;top:466px;width:290px;height:29px;padding:3px 0 0 34px;font-size:19px}
  .ph-roof{left:0;top:495px;width:214px;height:132px;background:linear-gradient(180deg,#dfe6ea,#c3cdd3 50%,#9aa8b0)}
  .ph-tower{left:216px;top:495px;width:164px;height:132px;background:linear-gradient(180deg,#cfd9e0,#aab6bc 55%,#6f7d75)}
  .ph-yard{left:0;top:0;width:380px;height:167px;background:linear-gradient(180deg,#c4ccd2,#98a49a 45%,#4e6f70)}
  .engineering{position:absolute;left:30px;top:187px;width:322px}
  .engineering h2{margin-bottom:7px}
  .engineering p{margin-bottom:13px}
  .ph-compressors{left:0;top:411px;width:380px;height:216px;background:linear-gradient(180deg,#d7dde2 0%,#aeb9c0 40%,#4f6e78 75%,#3d5863)}
  .label--survey{left:0;top:391px;width:313px;height:45px;padding:2px 0 0 29px;z-index:2}
  .label--survey .big{font-size:19px;display:block;line-height:1.2}
  .label--survey .small{font-family:"Open Sans",sans-serif;font-size:9.4px;display:block}
  .footer{height:50px;background:var(--orange);display:flex;align-items:center;color:var(--ink-on-orange);font-family:"Raleway",sans-serif;font-weight:600;font-size:13px}
  .footer .cell{width:380px;padding-left:27px}
  .footer .cell--mid{padding-left:33px}
  .brand{display:flex;align-items:center;gap:8px;padding-left:38px}
  .brand-mark{width:10px;height:10px;border-radius:50%;background:var(--ink-on-orange)}
  .brand-name{font-family:"Raleway",sans-serif;font-weight:600;font-size:12px;color:var(--ink-on-orange)}
</style>
</head>
<body>
<main class="spread">
  <div class="top-band"></div>
  <div class="panels">
    <section class="panel panel--left">
      <div class="experience">
        <h2>Experience</h2>
        <p>Thirty plus years in industrial, commercial, ammonia and freon refrigeration and air conditioning. Experienced in all aspects of refrigeration projects, from design concept through execution, with the ability to cost-effectively satisfy customer requirements within aggressive time frames.</p>
      </div>
      <div class="photo-row">
        <div class="photo ph-plant" role="img" aria-label="Photo of a compressor room with teal refrigeration units"></div>
        <div class="photo ph-tank" role="img" aria-label="Photo of an insulated refrigeration vessel and piping"></div>
        <div class="photo ph-room" role="img" aria-label="Photo of an evaporator installed in a cold storage room"></div>
      </div>
      <div class="label label--design">From Design Concept<br>Through Execution</div>
      <div class="projects">
        <h2>Major Projects Completed</h2>
        <ul>
          <li>675 TR, 1960 HP ammonia refrigeration system for a bakery.</li>
          <li>90 TR, 400 HP freon spiral blast freezer for meat<br>processing plant.</li>
          <li>920 TR, 1420 HP ammonia refrigeration system for meat processing facility.</li>
          <li>1300 TR freon chiller and glycol chiller and glycol<br>distribution system for a dairy processing plant.</li>
          <li>An ammonia refrigeration system for 560,000 sq. ft cold storage and food distribution facility.</li>
          <li>480 ton ice production facility.</li>
          <li>375 TR, 1500 HP ice-cream plant.</li>
        </ul>
      </div>
    </section>

    <section class="panel panel--mid">
      <div class="service">
        <h2>Service and Maintenance</h2>
        <p>24 hour Emergency Service - Ammonia and Freon. Customized maintenance program. Troubleshooting service and repair of refrigeration and HVAC systems including all mechanical, structural, electrical and control components. Compressor rebuilding as well as vibration and oil analysis. Refrigerant conversion and recovery.</p>
        <p>Build-up ammonia and freon refrigeration systems, packaged freon refrigeration units, blast freezing/cooling systems, spiral and tunnel freezers, holding freezers and coolers, evaporators, glycol and water chillers, ice production machines, process.</p>
        <p>Compressors, evaporative and air-cool condensers, recirculation packages, ammonia, water and glycol pumps, heat exchangers, control valves and regulators, electrical motors.</p>
        <p>Safety devices test, repair and calibration including: relief valves, leak detectors, pressure and temperature sensors, level.</p>
        <p>Packaged and split gas/electric air conditioners, heat pumps. Air handlers, exhaust fans, swamp coolers, water chillers, water towers and pumps. Exhaust and ventilation, humidification and dehumidification, clean rooms. Boilers and Boiler Piping. Refrigeration and Building Control and Automation.</p>
        <p>PLC, VFD, VSD, VAV.</p>
      </div>
      <div class="label label--emergency">24 hour Emergency Service</div>
      <div class="photo ph-roof" role="img" aria-label="Photo of insulated refrigeration piping on a rooftop"></div>
      <div class="photo ph-tower" role="img" aria-label="Photo of a rooftop cooling tower"></div>
    </section>

    <section class="panel panel--right">
      <div class="photo ph-yard" role="img" aria-label="Photo of rooftop mechanical equipment and compressor units"></div>
      <div class="engineering">
        <h2>Engineering Services</h2>
        <p>Design ammonia and freon systems. Build-up and packaged refrigeration systems. Liquid recirculating, flooded, and DX systems. Low and high temperature chillers. Glycol and chill water distribution systems.</p>
        <p>Energy saving and expansion projects. 3D FormStudio and DraftLine CAD drawings. Computerized control design and implementation, PLC, VFD.</p>
        <p>Mechanical integrity surveys, safety and hazard analysis, seismic assessment. Safety programs, PSM, RMP, CalARP, MOC, SOP. Regulatory Compliance and Professional training.</p>
      </div>
      <div class="label label--survey">
        <span class="big">Free survey and quote</span>
        <span class="small">on your refrigeration and air conditioning equipment needs.</span>
      </div>
      <div class="photo ph-compressors" role="img" aria-label="Photo of a compressor room with colour-coded piping"></div>
    </section>
  </div>
  <footer class="footer">
    <div class="cell">Get A Free Quote And Survey!</div>
    <div class="cell cell--mid">Customer Satisfaction Is Our Ultimate Goal!</div>
    <div class="cell brand">
      <span class="brand-mark"></span>
      <span class="brand-name">Northbay Cooling &amp; Climate Systems</span>
    </div>
  </footer>
</main>
</body>
</html>
```